Design 4 pages for an event discovery website

This is a contest for the design of 4 pages for an events discovery website. The feature is part of the new sign-up process.

Please see the attached document for a full scope, mockups and the parent category icons.

Target Market(s)

18-35 Australian event goers

Industry/Entity Type

Events

Number of Pages Required

4 page

```html
<!DOCTYPE html>
<html lang="en">
<head>
<meta charset="utf-8">
<title>Ventora – Sign Up 1 of 5</title>
<link rel="stylesheet" href="https://fonts.googleapis.com/css2?family=Open+Sans:wght@400;600;700&family=Arimo:wght@400&display=swap">
<style>
  :root {
    --bg-deep: #23242c;
    --bg-mid: #2c2d36;
    --glow-rose: rgba(150, 70, 90, 0.45);
    --glow-amber: rgba(150, 130, 80, 0.35);
    --glow-teal: rgba(40, 110, 90, 0.45);
    --text-light: #ffffff;
    --text-dark: #3a3a3a;
    --button-top: #efefef;
    --button-bottom: #dcdcdc;
    --button-border: #9a9a9a;
    --rule: rgba(0, 0, 0, 0.35);
    --rule-light: rgba(255, 255, 255, 0.08);
  }
  * { box-sizing: border-box; margin: 0; padding: 0; }
  html, body { width: 1200px; height: 656px; overflow: hidden; }
  body {
    position: relative;
    font-family: "Arimo", Arial, sans-serif;
    color: var(--text-light);
    background: var(--bg-deep);
  }
  .backdrop {
    position: absolute; inset: 0;
    background:
      radial-gradient(ellipse 260px 200px at 720px 260px, var(--glow-rose), transparent 70%),
      radial-gradient(ellipse 220px 260px at 1000px 180px, var(--glow-amber), transparent 70%),
      radial-gradient(ellipse 420px 160px at 420px 600px, var(--glow-teal), transparent 70%),
      radial-gradient(ellipse 200px 300px at 1140px 80px, rgba(120, 60, 80, 0.35), transparent 70%),
      linear-gradient(160deg, var(--bg-mid), var(--bg-deep));
  }
  .site-header {
    position: absolute; left: 0; top: 0; width: 1200px; height: 106px;
    border-bottom: 1px solid var(--rule);
    box-shadow: 0 1px 0 var(--rule-light);
  }
  .brand {
    position: absolute; left: 141px; top: 36px;
    font-family: "Open Sans", sans-serif; font-weight: 600;
    font-size: 29px; letter-spacing: 0.5px; line-height: 1;
  }
  .search {
    position: absolute; left: 664px; top: 33px; width: 234px; height: 42px;
    border: 1px solid rgba(255,255,255,0.85); border-radius: 21px;
    font-family: "Open Sans", sans-serif; font-weight: 600; font-size: 13px;
    padding: 0 0 0 22px; line-height: 40px;
  }
  .search svg { position: absolute; right: 22px; top: 14px; }
  .account-nav {
    position: absolute; left: 920px; top: 45px;
    font-family: "Open Sans", sans-serif; font-weight: 600; font-size: 14px;
    display: flex; gap: 16px; line-height: 16px;
  }
  .intro { position: absolute; left: 141px; top: 142px; }
  .intro h1 {
    font-family: "Open Sans", sans-serif; font-weight: 700; font-size: 23px;
    letter-spacing: 0.2px; line-height: 1;
  }
  .intro p { font-size: 15.5px; line-height: 28px; }
  .intro h1 + p { margin-top: 20px; }
  .link-row { position: absolute; left: 141px; display: flex; align-items: center; }
  .link-button {
    width: 267px; height: 52px;
    background: linear-gradient(var(--button-top), var(--button-bottom));
    border: 1px solid var(--button-border);
    display: flex; align-items: center;
    color: var(--text-dark); font-size: 15.5px;
  }
  .link-button .mark {
    width: 32px; height: 32px; margin: 0 10px 0 7px; border-radius: 5px;
    background: #8a8a8a; flex: none;
  }
  .link-button .divider {
    width: 1px; height: 36px; background: #bcbcbc; margin-right: 15px;
  }
  .link-status { margin-left: 20px; font-size: 14px; }
  .site-footer {
    position: absolute; left: 0; top: 583px; width: 1200px; height: 73px;
    border-top: 1px solid var(--rule);
    box-shadow: inset 0 1px 0 var(--rule-light);
  }
  .copyright { position: absolute; left: 141px; top: 34px; font-size: 11.5px; }
  .social { position: absolute; left: 840px; top: 19px; display: flex; gap: 9px; }
  .social span {
    width: 37px; height: 37px; border-radius: 50%;
    border: 1px solid rgba(255,255,255,0.85);
  }
</style>
</head>
<body>
  <div class="backdrop" role="img" aria-label="Abstract dark background with soft rose, amber and teal light streaks"></div>

  <header class="site-header">
    <div class="brand">VENTORA</div>
    <div class="search">Search
      <svg width="12" height="12" viewBox="0 0 12 12" aria-hidden="true">
        <circle cx="5" cy="5" r="3.6" fill="none" stroke="#fff" stroke-width="2"/>
        <line x1="7.6" y1="7.6" x2="11" y2="11" stroke="#fff" stroke-width="2.2" stroke-linecap="round"/>
      </svg>
    </div>
    <nav class="account-nav"><span>SIGN UP</span><span>|</span><span>LOG IN</span></nav>
  </header>

  <main>
    <section class="intro">
      <h1>SIGN UP 1 OF 5</h1>
      <p>Link in all Your other Social Media accounts and Music Players</p>
      <p>By Linking Your Accounts we Can Save You a Lot of Time by automatically determinigYour Interests</p>
    </section>

    <div class="link-row" style="top:280px">
      <div class="link-button"><span class="mark"></span><span class="divider"></span>Follow us on Chirpline</div>
      <span class="link-status">Linked in</span>
    </div>
    <div class="link-row" style="top:346px">
      <div class="link-button"><span class="mark"></span><span class="divider"></span>Follow us on snapgrid</div>
    </div>
    <div class="link-row" style="top:413px">
      <div class="link-button"><span class="mark"></span><span class="divider"></span>Follow us on Tunewave</div>
      <span class="link-status">We Don't Have that Featued get but have required Your interest</span>
    </div>
    <div class="link-row" style="top:481px">
      <div class="link-button"><span class="mark"></span><span class="divider"></span>Follow us on songvault</div>
    </div>
  </main>

  <footer class="site-footer">
    <p class="copyright">© Copy Rights 2015 Ventora.All Rights Reserved.</p>
    <div class="social" aria-label="Social links">
      <span></span><span></span><span></span><span></span><span></span>
    </div>
  </footer>
</body>
</html>
```